web page look and feel - B2B enterprise application

We have an enterprise application with 10 to 15 core pages and several supporting pages or popups. To start, we want the graphical design of the Users, Roles and Data Source pages and their supporting popups, wizards, etc. to be made beautiful. That is around 10 pages in total. There is a fair amount of redundancy among the pages. I have attached 5 screenshots. We very much want the pages to project a premium feel. That is absolutely essential. The color scheme is blue and sometimes yellow (only if it makes the page look better) plus black, gray and white. If the design of these screens goes well, we would expand the project to continue with other pages. The core of what we are looking for is graphic in nature but we are open to workflow suggestions if you have them. The Roles screen needs some improvements to the layout. I am looking for everything that includes icons, fonts, spacing, etc. I assume getting to the final design will take some back and forth with multiple revisions.

Target Market(s)

Large Enterprises

Number of Pages Required

5+ page

Requirements
Must have
• Premium feel

```html
<!DOCTYPE html>
<html lang="en">
<head>
<meta charset="utf-8">
<title>Users – Norvale Data</title>
<link rel="stylesheet" href="https://fonts.googleapis.com/css2?family=Dosis:wght@400;500;600;700&family=Montserrat:wght@300;400;500&display=swap">
<style>
:root{
  --bg-main:#1d2735;
  --bg-side:#1f2b3a;
  --bg-top:#243143;
  --bg-row:#28374b;
  --bg-row-alt:#2b3b50;
  --bg-head:#212c3b;
  --bg-nav-active:#2e3c4f;
  --line:#36465b;
  --line-soft:#2f3e52;
  --text:#e8edf3;
  --text-soft:#c4ceda;
  --text-dim:#8795a8;
  --blue:#1f78e0;
  --blue-bright:#2b8cff;
  --teal:#22d3a4;
  --orange:#ff6a1a;
}
*{box-sizing:border-box;margin:0;padding:0}
html,body{width:1200px;height:786px;overflow:hidden;background:var(--bg-main)}
body{font-family:"Dosis",sans-serif;color:var(--text);position:relative}
svg{display:block}

/* brand + top bar */
.brand{position:absolute;left:0;top:0;width:300px;height:80px;background:var(--bg-top);border-right:2px solid #18212d;display:flex;align-items:center;padding-left:42px}
.brand-mark{width:20px;height:20px;border-radius:50%;background:var(--text);margin-right:10px}
.brand-name{font-family:"Dosis",sans-serif;font-weight:600;font-size:24px;color:var(--text)}
.menu-toggle{position:absolute;left:243px;top:33px}
.topbar{position:absolute;left:302px;top:0;right:0;height:80px;background:var(--bg-top);border-bottom:2px solid #18212d}
.topbar-icons{position:absolute;left:490px;top:26px;display:flex;gap:22px}
.topbar-icons .icon{width:28px;height:28px;position:relative}
.notify-dot{position:absolute;right:-2px;top:2px;width:9px;height:9px;border-radius:50%;background:var(--orange)}
.account{position:absolute;left:740px;top:26px;display:flex;align-items:center;gap:10px;font-weight:600;font-size:18px}

/* sidebar */
.sidebar{position:absolute;left:0;top:82px;width:300px;bottom:0;background:var(--bg-side)}
.profile{position:absolute;left:40px;top:18px;display:flex;gap:10px}
.avatar{width:40px;height:40px;border-radius:50%;background:radial-gradient(circle at 50% 40%,#c79a7f,#6a4a3a)}
.profile-name{font-weight:500;font-size:16px;line-height:18px;margin-top:1px}
.profile-email{font-family:"Montserrat",sans-serif;font-size:12px;color:var(--text-dim);margin-top:3px}
.profile-rule{position:absolute;left:20px;top:78px;width:260px;height:1px;background:var(--line)}
.nav{position:absolute;left:20px;top:94px;width:280px;list-style:none}
.nav-item{position:relative;height:33px;display:flex;align-items:center;font-size:15px;color:var(--text-soft);padding-left:20px}
.nav-item.group{background:var(--bg-nav-active);border-right:4px solid var(--blue);color:var(--text)}
.nav-item.sub{padding-left:42px}
.nav-item .ico{width:18px;height:18px;margin-right:14px}
.nav-item.sub .ico{width:16px;height:16px;margin-right:10px}
.nav-item .chev{position:absolute;right:36px}
.gap{height:-1px}
.clock-row{position:absolute;left:30px;top:576px;width:240px;display:flex;justify-content:space-between;font-weight:600;font-size:15px}
.clock-row span{display:flex;align-items:center;gap:10px}

/* main */
.page-title{position:absolute;left:329px;top:114px;font-family:"Montserrat",sans-serif;font-weight:300;font-size:32px}
.btn-add{position:absolute;left:433px;top:140px;height:28px;width:64px;background:var(--blue);border-radius:2px;display:flex;align-items:center;justify-content:center;gap:5px;font-size:15px;font-weight:500}
.filter{position:absolute;left:769px;top:127px}
.search-input{position:absolute;left:792px;top:116px;width:255px;height:37px;border-radius:19px;background:var(--bg-head);font-family:"Montserrat",sans-serif;font-size:11px;color:#4d5b6e;padding:11px 16px;font-weight:500}
.btn-search{position:absolute;left:1065px;top:115px;width:105px;height:38px;border:2px solid var(--blue);border-radius:19px;display:flex;align-items:center;justify-content:center;gap:6px;font-family:"Montserrat",sans-serif;font-size:12px;font-weight:500}

.users-table{position:absolute;left:330px;top:188px;width:840px}
.row{display:grid;grid-template-columns:40px repeat(5,137px) 115px;height:39px;background:var(--bg-row);border-bottom:1px solid var(--line-soft)}
.row>div{display:flex;align-items:center;justify-content:center;font-size:15px;color:var(--text-soft);border-left:1px solid var(--line-soft)}
.row>div:first-child{border-left:none}
.row.head{background:var(--bg-head)}
.row.head>div{font-weight:600;font-size:16px;color:var(--text)}
.actions{gap:9px}
.act{width:20px;height:20px;background:var(--blue-bright);border-radius:2px;display:flex;align-items:center;justify-content:center}

.detail{background:var(--bg-row-alt)}
.detail-row{display:grid;grid-template-columns:420px 420px;height:39px;border-bottom:1px solid var(--line-soft)}
.detail-row>div{display:flex;align-items:center;justify-content:center;font-size:15px;color:var(--text-soft);gap:8px}
.detail-row>div+div{border-left:1px solid var(--line-soft)}
.detail-row.sub-head{background:var(--bg-head)}
.detail-row.sub-head>div{color:var(--text)}
.detail-row .muted{color:var(--text-dim)}
.perm{display:flex;align-items:center;gap:5px;margin:0 8px;color:var(--text-soft)}
.detail-edit{height:39px;background:var(--bg-head);display:flex;align-items:center;justify-content:center;font-weight:600;font-size:15px}
.spacer{height:11px;background:var(--bg-main)}

.pager{position:absolute;left:676px;top:736px;display:flex;align-items:center;gap:6px;font-weight:600;font-size:15px;color:var(--text-dim)}
.pager .current{color:var(--text)}
.page-size{position:absolute;left:787px;top:732px;width:32px;height:32px;border-radius:50%;background:#2f3e52;font-weight:600;font-size:13px;text-align:center;line-height:13px;padding-top:4px}
</style>
</head>
<body>

<header class="brand">
  <span class="brand-mark"></span><span class="brand-name">Norvale Data</span>
  <svg class="menu-toggle" width="16" height="14" viewBox="0 0 16 14"><path d="M0 1h16M0 7h16M0 13h16" stroke="#fff" stroke-width="2.4"/></svg>
</header>

<div class="topbar">
  <div class="topbar-icons">
    <svg class="icon" viewBox="0 0 28 28"><path d="M4 20a10 10 0 0 1 20 0" fill="none" stroke="#fff" stroke-width="2.6"/><path d="M14 20l5-7" stroke="#fff" stroke-width="2.6"/></svg>
    <svg class="icon" viewBox="0 0 28 28"><path d="M5 24L19 10" stroke="#fff" stroke-width="3"/><path d="M21 3v4M19 5h4M25 11v3M23.5 12.5h3M14 4v2M13 5h2" stroke="#fff" stroke-width="1.5"/></svg>
    <svg class="icon" viewBox="0 0 28 28"><circle cx="13" cy="13" r="12" fill="#8c97a6"/><path d="M9.5 10a3.5 3.5 0 1 1 5 3c-1.3.7-1.5 1.3-1.5 2.5" fill="none" stroke="#1f2b3a" stroke-width="2.6"/><circle cx="13" cy="19.5" r="1.6" fill="#1f2b3a"/><path d="M20 17v8l2-1.5 2 1.5v-5l-2-1" fill="#fff"/></svg>
    <div class="icon">
      <svg viewBox="0 0 28 28" width="28" height="28"><circle cx="10" cy="11" r="6" fill="none" stroke="#fff" stroke-width="3.5" stroke-dasharray="3 2"/><circle cx="10" cy="11" r="2" fill="#fff"/><circle cx="19" cy="21" r="4" fill="none" stroke="#fff" stroke-width="3" stroke-dasharray="2.5 1.5"/></svg>
      <span class="notify-dot"></span>
    </div>
  </div>
  <div class="account">
    <svg width="20" height="24" viewBox="0 0 20 24"><circle cx="10" cy="6" r="6" fill="#fff"/><path d="M0 24c0-7 4-10 10-10s10 3 10 10z" fill="#fff"/></svg>
    Dana Reyes
    <svg width="12" height="8" viewBox="0 0 12 8" style="margin-left:6px"><path d="M1 1l5 5 5-5" fill="none" stroke="#fff" stroke-width="1.5"/></svg>
  </div>
</div>

<aside class="sidebar">
  <div class="profile">
    <div class="avatar" role="img" aria-label="Profile photo of Dana Reyes"></div>
    <div>
      <div class="profile-name">Dana Reyes</div>
      <div class="profile-email">dana.reyes@example.com</div>
    </div>
  </div>
  <div class="profile-rule"></div>

  <ul class="nav">
    <li class="nav-item group"><svg class="ico" viewBox="0 0 18 18"><circle cx="9" cy="5" r="4" fill="#fff"/><path d="M2 18c0-5 3-7 7-7s7 2 7 7z" fill="#fff"/></svg>User<svg class="chev" width="10" height="6" viewBox="0 0 10 6"><path d="M1 1l4 4 4-4" fill="none" stroke="#fff" stroke-width="1.3"/></svg></li>
    <li class="nav-item sub"><svg class="ico" viewBox="0 0 16 16"><circle cx="8" cy="5" r="3.5" fill="none" stroke="#fff" stroke-width="1.2"/><path d="M1.5 15.5c0-4 3-6 6.5-6s6.5 2 6.5 6z" fill="none" stroke="#fff" stroke-width="1.2"/></svg>Roles</li>
    <li class="nav-item sub"><svg class="ico" viewBox="0 0 16 16"><path d="M8 1.5c-3 0-4.5 2.5-4.5 5v3L1.5 13h13l-2-3.5v-3c0-2.5-1.5-5-4.5-5zM6.5 14.5h3" fill="none" stroke="#fff" stroke-width="1.2"/></svg>Notification Groups</li>
    <li class="nav-item group"><svg class="ico" viewBox="0 0 18 18"><rect x="1" y="1" width="16" height="4" fill="#fff"/><rect x="1" y="7" width="16" height="4" fill="#fff"/><path d="M9 12v3M3 16h12" stroke="#fff" stroke-width="1.5"/></svg>Data Source<svg class="chev" width="10" height="6" viewBox="0 0 10 6"><path d="M1 1l4 4 4-4" fill="none" stroke="#fff" stroke-width="1.3"/></svg></li>
    <li class="nav-item sub"><svg class="ico" viewBox="0 0 16 16"><path d="M6 1.5h8v13H6M1 8h9M7 5l3 3-3 3" fill="none" stroke="#fff" stroke-width="1.2"/></svg>Data Object Relationship</li>
    <li class="nav-item"><svg class="ico" viewBox="0 0 18 18"><rect x="0" y="0" width="8" height="18" fill="#fff"/><rect x="10" y="0" width="8" height="8" fill="#fff"/><rect x="10" y="10" width="8" height="8" fill="#fff"/></svg>Data Sets</li>
    <li class="nav-item"><svg class="ico" viewBox="0 0 18 18"><rect x="0" y="0" width="6" height="18" fill="#fff"/><path d="M8 2h10M8 6h10M8 10h10M8 14h10" stroke="#fff" stroke-width="2"/></svg>Rule Sets</li>
    <li class="nav-item"><svg class="ico" viewBox="0 0 18 18"><circle cx="9" cy="9" r="8" fill="none" stroke="#fff" stroke-width="1.6"/><path d="M9 4v5l3 2" fill="none" stroke="#fff" stroke-width="1.6"/></svg>Schedule</li>
    <li class="nav-item group"><svg class="ico" viewBox="0 0 18 18"><path d="M3 8a6 6 0 0 1 11-3M15 10a6 6 0 0 1-11 3" fill="none" stroke="#fff" stroke-width="1.6"/><path d="M14 1v4h-4M4 17v-4h4" fill="none" stroke="#fff" stroke-width="1.6"/></svg>Metadata Import/Export<svg class="chev" width="10" height="6" viewBox="0 0 10 6"><path d="M1 1l4 4 4-4" fill="none" stroke="#fff" stroke-width="1.3"/></svg></li>
    <li class="nav-item sub"><svg class="ico" viewBox="0 0 16 16"><path d="M8 1v13M3 9l5 5 5-5" fill="none" stroke="#fff" stroke-width="1.4"/></svg>Import</li>
    <li class="nav-item sub"><svg class="ico" viewBox="0 0 16 16"><path d="M8 15V2M3 7l5-5 5 5" fill="none" stroke="#fff" stroke-width="1.4"/></svg>Export</li>
  </ul>

  <div class="clock-row">
    <span><svg width="24" height="26" viewBox="0 0 24 26"><rect x="1.5" y="3.5" width="21" height="21" rx="2" fill="none" stroke="#fff" stroke-width="2"/><path d="M1.5 8h21M6 1v5M18 1v5" stroke="#fff" stroke-width="2"/><text x="12" y="22" font-family="Dosis" font-weight="700" font-size="12" fill="#fff" text-anchor="middle">5</text></svg>July 05</span>
    <span><svg width="24" height="24" viewBox="0 0 24 24"><circle cx="12" cy="12" r="10.5" fill="none" stroke="#fff" stroke-width="2"/><path d="M12 5v7l4 3" fill="none" stroke="#fff" stroke-width="2"/></svg>18:36</span>
  </div>
</aside>

<main>
  <h1 class="page-title">Users</h1>
  <div class="btn-add"><svg width="15" height="15" viewBox="0 0 15 15"><circle cx="7.5" cy="7.5" r="6.5" fill="none" stroke="#fff" stroke-width="1.3"/><path d="M7.5 4v7M4 7.5h7" stroke="#fff" stroke-width="1.3"/></svg>Add</div>

  <svg class="filter" width="14" height="14" viewBox="0 0 14 14"><path d="M0 0h14L8.5 6.5V14l-3-2V6.5z" fill="#a7b2c0"/></svg>
  <div class="search-input">Placeholder text goes here...</div>
  <div class="btn-search"><svg width="11" height="11" viewBox="0 0 11 11"><circle cx="4.5" cy="4.5" r="3.5" fill="none" stroke="#fff" stroke-width="1.4"/><path d="M7 7l3.5 3.5" stroke="#fff" stroke-width="1.4"/></svg>Search</div>

  <section class="users-table">
    <div class="row head"><div></div><div>First Name</div><div>Last Name</div><div>Username</div><div>Email</div><div>Status</div><div>Edit</div></div>

    <div class="row"><div><svg width="6" height="10" viewBox="0 0 6 10"><path d="M1 1l4 4-4 4" fill="none" stroke="#8795a8" stroke-width="1.4"/></svg></div><div>Test</div><div>Test</div><div>test.1</div><div>test@example.net</div><div>Active</div>
      <div class="actions"><span class="act"><svg width="12" height="12" viewBox="0 0 12 12"><path d="M2 9l6-6 1.5 1.5-6 6H2zM1 11.5h10" fill="none" stroke="#fff" stroke-width="1.1"/></svg></span><span class="act"><svg width="12" height="12" viewBox="0 0 12 12"><rect x="4" y="1" width="7" height="8" fill="none" stroke="#fff" stroke-width="1.2"/><path d="M2 3v8h7" fill="none" stroke="#fff" stroke-width="1.2"/></svg></span><span class="act"><svg width="12" height="12" viewBox="0 0 12 12"><path d="M1 2.5h10M4 2.5V1h4v1.5M2.5 2.5l.7 9h5.6l.7-9M5 5v4M7 5v4" fill="none" stroke="#fff" stroke-width="1.1"/></svg></span></div>
    </div>

    <div class="detail">
      <div class="detail-row sub-head"><div>Object</div><div>Permissions</div></div>
      <div class="detail-row"><div>System Settings</div><div>
        <span class="perm"><svg width="19" height="19" viewBox="0 0 19 19"><circle cx="9.5" cy="9.5" r="9.5" fill="var(--teal)"/><path d="M5 9.5l3 3 6-6" fill="none" stroke="#1d2735" stroke-width="2.2"/></svg>Read</span>
        <span class="perm"><svg width="19" height="19" viewBox="0 0 19 19"><circle cx="9.5" cy="9.5" r="9.5" fill="var(--teal)"/><path d="M5 9.5l3 3 6-6" fill="none" stroke="#1d2735" stroke-width="2.2"/></svg>Write</span></div></div>
      <div class="detail-row"><div>Users</div><div>
        <span class="perm"><svg width="19" height="19" viewBox="0 0 19 19"><circle cx="9.5" cy="9.5" r="9.5" fill="var(--teal)"/><path d="M5 9.5l3 3 6-6" fill="none" stroke="#1d2735" stroke-width="2.2"/></svg>Read</span>
        <span class="perm"><svg width="19" height="19" viewBox="0 0 19 19"><circle cx="9.5" cy="9.5" r="9.5" fill="var(--teal)"/><path d="M5 9.5l3 3 6-6" fill="none" stroke="#1d2735" stroke-width="2.2"/></svg>Write</span></div></div>
      <div class="detail-row sub-head"><div>Data Source</div><div>Role</div></div>
      <div class="detail-row"><div class="muted">All Data Sources</div><div class="muted">All Administrator</div></div>
      <div class="detail-edit">Edit</div>
    </div>

    <div class="spacer"></div>

    <div class="row"><div><svg width="10" height="6" viewBox="0 0 10 6"><path d="M1 1l4 4 4-4" fill="none" stroke="#8795a8" stroke-width="1.4"/></svg></div><div>Test</div><div>Test</div><div>test.1</div><div>test@example.net</div><div>Active</div>
      <div class="actions"><span class="act"><svg width="12" height="12" viewBox="0 0 12 12"><path d="M2 9l6-6 1.5 1.5-6 6H2zM1 11.5h10" fill="none" stroke="#fff" stroke-width="1.1"/></svg></span><span class="act"><svg width="12" height="12" viewBox="0 0 12 12"><rect x="4" y="1" width="7" height="8" fill="none" stroke="#fff" stroke-width="1.2"/><path d="M2 3v8h7" fill="none" stroke="#fff" stroke-width="1.2"/></svg></span><span class="act"><svg width="12" height="12" viewBox="0 0 12 12"><path d="M1 2.5h10M4 2.5V1h4v1.5M2.5 2.5l.7 9h5.6l.7-9M5 5v4M7 5v4" fill="none" stroke="#fff" stroke-width="1.1"/></svg></span></div></div>
    <div class="row"><div><svg width="10" height="6" viewBox="0 0 10 6"><path d="M1 1l4 4 4-4" fill="none" stroke="#8795a8" stroke-width="1.4"/></svg></div><div>Test</div><div>Test</div><div>test.1</div><div>test@example.net</div><div>Active</div>
      <div class="actions"><span class="act"><svg width="12" height="12" viewBox="0 0 12 12"><path d="M2 9l6-6 1.5 1.5-6 6H2zM1 11.5h10" fill="none" stroke="#fff" stroke-width="1.1"/></svg></span><span class="act"><svg width="12" height="12" viewBox="0 0 12 12"><rect x="4" y="1" width="7" height="8" fill="none" stroke="#fff" stroke-width="1.2"/><path d="M2 3v8h7" fill="none" stroke="#fff" stroke-width="1.2"/></svg></span><span class="act"><svg width="12" height="12" viewBox="0 0 12 12"><path d="M1 2.5h10M4 2.5V1h4v1.5M2.5 2.5l.7 9h5.6l.7-9M5 5v4M7 5v4" fill="none" stroke="#fff" stroke-width="1.1"/></svg></span></div></div>
    <div class="row"><div><svg width="10" height="6" viewBox="0 0 10 6"><path d="M1 1l4 4 4-4" fill="none" stroke="#8795a8" stroke-width="1.4"/></svg></div><div>Test</div><div>Test</div><div>test.1</div><div>test@example.net</div><div>Active</div>
      <div class="actions"><span class="act"><svg width="12" height="12" viewBox="0 0 12 12"><path d="M2 9l6-6 1.5 1.5-6 6H2zM1 11.5h10" fill="none" stroke="#fff" stroke-width="1.1"/></svg></span><span class="act"><svg width="12" height="12" viewBox="0 0 12 12"><rect x="4" y="1" width="7" height="8" fill="none" stroke="#fff" stroke-width="1.2"/><path d="M2 3v8h7" fill="none" stroke="#fff" stroke-width="1.2"/></svg></span><span class="act"><svg width="12" height="12" viewBox="0 0 12 12"><path d="M1 2.5h10M4 2.5V1h4v1.5M2.5 2.5l.7 9h5.6l.7-9M5 5v4M7 5v4" fill="none" stroke="#fff" stroke-width="1.1"/></svg></span></div></div>
    <div class="row"><div><svg width="10" height="6" viewBox="0 0 10 6"><path d="M1 1l4 4 4-4" fill="none" stroke="#8795a8" stroke-width="1.4"/></svg></div><div>Test</div><div>Test</div><div>test.1</div><div>test@example.net</div><div>Active</div>
      <div class="actions"><span class="act"><svg width="12" height="12" viewBox="0 0 12 12"><path d="M2 9l6-6 1.5 1.5-6 6H2zM1 11.5h10" fill="none" stroke="#fff" stroke-width="1.1"/></svg></span><span class="act"><svg width="12" height="12" viewBox="0 0 12 12"><rect x="4" y="1" width="7" height="8" fill="none" stroke="#fff" stroke-width="1.2"/><path d="M2 3v8h7" fill="none" stroke="#fff" stroke-width="1.2"/></svg></span><span class="act"><svg width="12" height="12" viewBox="0 0 12 12"><path d="M1 2.5h10M4 2.5V1h4v1.5M2.5 2.5l.7 9h5.6l.7-9M5 5v4M7 5v4" fill="none" stroke="#fff" stroke-width="1.1"/></svg></span></div></div>
    <div class="row"><div><svg width="10" height="6" viewBox="0 0 10 6"><path d="M1 1l4 4 4-4" fill="none" stroke="#8795a8" stroke-width="1.4"/></svg></div><div>Test</div><div>Test</div><div>test.1</div><div>test@example.net</div><div>Active</div>
      <div class="actions"><span class="act"><svg width="12" height="12" viewBox="0 0 12 12"><path d="M2 9l6-6 1.5 1.5-6 6H2zM1 11.5h10" fill="none" stroke="#fff" stroke-width="1.1"/></svg></span><span class="act"><svg width="12" height="12" viewBox="0 0 12 12"><rect x="4" y="1" width="7" height="8" fill="none" stroke="#fff" stroke-width="1.2"/><path d="M2 3v8h7" fill="none" stroke="#fff" stroke-width="1.2"/></svg></span><span class="act"><svg width="12" height="12" viewBox="0 0 12 12"><path d="M1 2.5h10M4 2.5V1h4v1.5M2.5 2.5l.7 9h5.6l.7-9M5 5v4M7 5v4" fill="none" stroke="#fff" stroke-width="1.1"/></svg></span></div></div>
  </section>

  <nav class="pager">
    <svg width="7" height="11" viewBox="0 0 7 11"><path d="M6 1L1.5 5.5 6 10" fill="none" stroke="#fff" stroke-width="1.6"/></svg>
    <span class="current">1</span><span>2</span><span>3</span><span>4</span>
    <svg width="7" height="11" viewBox="0 0 7 11"><path d="M1 1l4.5 4.5L1 10" fill="none" stroke="#fff" stroke-width="1.6"/></svg>
  </nav>
  <div class="page-size">20<svg width="10" height="6" viewBox="0 0 10 6" style="margin:2px auto 0"><path d="M1 1l4 4 4-4" fill="none" stroke="#fff" stroke-width="1.6"/></svg></div>
</main>

</body>
</html>
```